Quillfern Vaults - Direct Mailer / Flyer

We are excited to announce the launch of our new company, Quillfern Vaults, a premier cohosting facility and data center dedicated to Cryptocurrency Miners. Our website, https://quillfernvaults.example, provides detailed information about our offerings and showcases the innovative design schemes for the entire project.

Quillfern Vaults stands out in the industry by offering both GPU Hosting and ASIC Hosting services in our state-of-the-art facility, equipped with an impressive 17 Megawatts of available power. What sets us apart is our unique billing system based on actual metered power usage. We charge $0.08 for ASIC miners and $0.09 for GPU miners, ensuring cost-effectiveness and transparency for our clients.

Our commitment to excellence is evident in our use of cutting-edge technology, top-notch facilities, and strategic partnerships. These elements come together to deliver exceptional solutions tailored for real-world applications in the cryptocurrency space.

As part of our promotional efforts, we are developing a direct mailer/flyer to introduce Quillfern Vaults to a wider audience. This promotional material will also serve as a handout at events, to potential customers, and more. We welcome creative ideas and suggestions to maximize the versatility of this design and reach diverse target audiences effectively.

For a comprehensive overview of our services and to explore our design concepts, please visit https://quillfernvaults.example. Quillfern Vaults is poised to revolutionize the mining industry, and we look forward to partnering with you for success in the digital currency era.

```html
<!DOCTYPE html>
<html lang="en">
<head>
<meta charset="utf-8">
<title>Quillfern Vaults – Flyer</title>
<link rel="stylesheet" href="https://fonts.googleapis.com/css2?family=Inter:wght@300;400;500;600;700;800&display=swap">
<style>
  :root{
    --bg:#3b3b3b;
    --blue:#2342a8;
    --blue-light:#3152c0;
    --yellow:#f5cc00;
    --yellow-soft:#f9dc3a;
    --ink:#0d0d12;
    --card:#e9ebf3;
    --paper:#f6f6f8;
    --muted:#2b2f3c;
    --green:#1f8a3b;
    --white:#ffffff;
  }
  *{box-sizing:border-box;margin:0;padding:0}
  html,body{width:1200px;height:800px;overflow:hidden}
  body{background:var(--bg);font-family:"Inter",sans-serif;position:relative}
  .flyer{position:absolute;left:332px;top:22px;width:536px;height:756px;background:var(--paper);overflow:hidden;box-shadow:0 10px 30px rgba(0,0,0,.35)}

  /* header */
  .hero{position:absolute;left:0;top:0;width:536px;height:248px;background:var(--blue)}
  .hero-art{position:absolute;right:0;top:0;width:230px;height:248px;background:linear-gradient(135deg,var(--blue) 0%,var(--blue-light) 55%,var(--blue) 100%)}
  .brand{position:absolute;left:27px;top:24px;display:flex;align-items:center;gap:8px;color:var(--white);font-weight:800;font-size:20px;letter-spacing:.5px;text-transform:uppercase}
  .brand-mark{width:20px;height:20px;background:var(--white);border-radius:2px}
  .hero-title{position:absolute;left:27px;top:72px;color:var(--white);font-weight:800;font-size:37px;line-height:39px;letter-spacing:-.3px}
  .hero-rule{position:absolute;left:27px;top:196px;width:108px;height:2px;background:var(--yellow)}
  .hero-sub{position:absolute;left:27px;top:205px;color:var(--white);font-weight:300;font-size:10.8px;line-height:13px;width:230px}
  .tag{position:absolute;display:flex;align-items:center;gap:5px;background:var(--white);color:var(--blue);font-weight:600;font-size:7.6px;height:23px;padding:0 7px;border-radius:2px;box-shadow:0 1px 3px rgba(0,0,0,.2);white-space:nowrap}
  .tag svg{width:10px;height:10px}

  /* services */
  .service{position:absolute;top:263px;width:100px;height:117px;background:var(--card);border-radius:8px;padding:12px 4px 12px 10px}
  .service svg{width:24px;height:24px;color:var(--blue)}
  .service h3{margin-top:10px;color:var(--blue);font-weight:600;font-size:9.8px;letter-spacing:-.2px;white-space:nowrap}
  .service p{margin-top:8px;color:var(--muted);font-size:5.6px;line-height:7.5px;width:82px}
  .badge{position:absolute;top:-6px;right:16px;font-size:4.6px;font-weight:800;padding:2px 4px;border-radius:2px;text-transform:uppercase}
  .badge-popular{background:var(--yellow);color:var(--ink)}
  .badge-value{background:var(--green);color:var(--white)}

  /* yellow band */
  .solutions{position:absolute;left:0;top:393px;width:536px;height:162px;background:linear-gradient(90deg,var(--yellow) 0%,var(--yellow) 60%,var(--yellow-soft) 100%)}
  .solutions h2{position:absolute;left:26px;top:11px;font-weight:800;font-size:27px;color:var(--ink);letter-spacing:-.4px;white-space:nowrap}
  .solutions p{position:absolute;left:27px;top:49px;width:490px;font-size:9px;line-height:12.5px;color:var(--ink)}
  .stat{position:absolute;top:83px;width:150px;height:71px;background:var(--ink);border-radius:4px;display:flex;align-items:center;gap:8px;padding:0 8px}
  .stat svg{width:24px;height:24px;color:var(--yellow);flex:none}
  .stat strong{display:block;color:var(--yellow);font-weight:700;font-size:15.5px;letter-spacing:-.2px;white-space:nowrap}
  .stat span{display:block;color:var(--yellow);font-weight:300;font-size:9.4px;line-height:11.5px}

  /* features */
  .features-title{position:absolute;left:27px;top:568px;font-weight:800;font-size:18.6px;color:var(--blue);letter-spacing:-.2px;white-space:nowrap}
  .feature{position:absolute;height:47px;background:var(--card);border-radius:5px;padding:6px 8px 6px 11px}
  .feature h4{display:flex;align-items:center;gap:4px;font-weight:500;font-size:10px;letter-spacing:-.2px;color:var(--ink);white-space:nowrap}
  .feature h4 svg{width:9px;height:9px;color:var(--blue);flex:none}
  .feature p{margin-top:3px;font-size:4.9px;line-height:6.4px;color:var(--muted);width:110px}
  .feature.wide p{width:128px}

  .footer{position:absolute;left:0;top:712px;width:536px;height:44px;background:var(--blue);display:flex;align-items:center;justify-content:center;color:var(--white);font-weight:600;font-size:18px;letter-spacing:1.2px}
</style>
</head>
<body>
<main class="flyer">
  <header class="hero">
    <div class="hero-art" role="img" aria-label="Decorative circuit-line pattern in blue and yellow"></div>
    <div class="brand"><span class="brand-mark"></span>Quillfern Vaults</div>
    <h1 class="hero-title">Transform<br>Mining with<br>Cohosting</h1>
    <div class="hero-rule"></div>
    <p class="hero-sub">Miners deserve the best - choose the hosting company that delivers excellence!</p>

    <div class="tag" style="left:338px;top:44px"><svg viewBox="0 0 24 24" fill="none" stroke="currentColor" stroke-width="2.4"><path d="M12 3l8 3v6c0 5-4 8-8 9-4-1-8-4-8-9V6z"/><path d="M9 12l2 2 4-4"/></svg>New Secure Facility</div>
    <div class="tag" style="left:428px;top:88px"><svg viewBox="0 0 24 24" fill="none" stroke="currentColor" stroke-width="2.4"><path d="M3 18a9 9 0 0118 0z"/><path d="M12 18l4-5"/></svg>Speedy Support</div>
    <div class="tag" style="left:334px;top:128px"><svg viewBox="0 0 24 24" fill="none" stroke="currentColor" stroke-width="2.4"><path d="M5 19l4-4M14 4l6 0 0 6-8 8-6-6z"/></svg>99.45% Uptime</div>
    <div class="tag" style="left:422px;top:178px"><svg viewBox="0 0 24 24" fill="none" stroke="currentColor" stroke-width="2.4"><path d="M7 17a5 5 0 01-.5-10A6 6 0 0118 9a4 4 0 010 8z"/></svg>24/7 Remote Access</div>
  </header>

  <section class="services">
    <article class="service" style="left:30px">
      <svg viewBox="0 0 24 24" fill="none" stroke="currentColor" stroke-width="1.8"><rect x="3" y="8" width="18" height="9" rx="1" transform="rotate(-40 12 12)"/><circle cx="9" cy="13" r="1.5"/><circle cx="12" cy="11" r="1.5"/><circle cx="15" cy="9" r="1.5"/></svg>
      <h3>GPU Hosting</h3>
      <p>Begin your GPU Hosting journey with rates starting at $0.09 kWh, accepting all equipment.</p>
    </article>
    <article class="service" style="left:157px">
      <span class="badge badge-popular">Most Popular</span>
      <svg viewBox="0 0 24 24" fill="none" stroke="currentColor" stroke-width="1.8"><rect x="6" y="6" width="12" height="12"/><rect x="9" y="9" width="6" height="6"/><path d="M9 3v3M12 3v3M15 3v3M9 18v3M12 18v3M15 18v3M3 9h3M3 12h3M3 15h3M18 9h3M18 12h3M18 15h3"/></svg>
      <h3>ASIC Hosting</h3>
      <p>Get your ASICs directly from us or send yours in today, starting at an all-in rate of $0.08 kWh.</p>
    </article>
    <article class="service" style="left:284px">
      <svg viewBox="0 0 24 24" fill="none" stroke="currentColor" stroke-width="1.8"><rect x="3" y="3" width="18" height="18" rx="2"/><circle cx="12" cy="12" r="6"/><circle cx="12" cy="12" r="2"/><path d="M8 8l8 8M16 8l-8 8"/></svg>
      <h3>Mining Hardware</h3>
      <p>Looking for mining hardware? Our equipment comes with no additional markup, ever.</p>
    </article>
    <article class="service" style="left:411px">
      <span class="badge badge-value">Best Value</span>
      <svg viewBox="0 0 24 24" fill="none" stroke="currentColor" stroke-width="1.8"><rect x="5" y="3" width="14" height="18" rx="1"/><path d="M8 7h8M9 16l3-3 2 2 2-3"/></svg>
      <h3>Crypto Consulting</h3>
      <p>Enjoy complete White Glove Services for setup,insuance, and tax consulting.</p>
    </article>
  </section>

  <section class="solutions">
    <h2>Real Solutions For Real Applications</h2>
    <p>Quillfern Vaults has committed to leveraging cutting-edge technology, state-of-the-art facilities, and strategic partnerships to deliver exceptional solutions tailored for real-world applications in the cryptocurrency space.</p>
    <div class="stat" style="left:28px">
      <svg viewBox="0 0 24 24" fill="none" stroke="currentColor" stroke-width="1.6"><rect x="3" y="14" width="18" height="6"/><rect x="6" y="9" width="5" height="5"/><rect x="13" y="4" width="5" height="5"/><path d="M13 9v5"/></svg>
      <div><strong>4,000,000+</strong><span>watts available for hosting</span></div>
    </div>
    <div class="stat" style="left:196px">
      <svg viewBox="0 0 24 24" fill="none" stroke="currentColor" stroke-width="1.6"><circle cx="11" cy="11" r="8"/><path d="M3 11h16M11 3c3 3 3 13 0 16M11 3c-3 3-3 13 0 16"/><circle cx="18" cy="18" r="2.5"/></svg>
      <div><strong>2,000,000+</strong><span>watts of green energy being produced</span></div>
    </div>
  </section>

  <h2 class="features-title">HOSTING TAILORED TO YOUR NEEDS</h2>
  <section class="features">
    <article class="feature" style="left:28px;top:599px;width:149px">
      <h4><svg viewBox="0 0 24 24" fill="none" stroke="currentColor" stroke-width="2.4"><path d="M13 2L5 14h6l-1 8 8-12h-6z"/></svg>99.45% Uptime</h4>
      <p>We boast an impressive uptime of 99.45% on average, ensuring consistent availability and reliability for users</p>
    </article>
    <article class="feature" style="left:193px;top:599px;width:149px">
      <h4><svg viewBox="0 0 24 24" fill="none" stroke="currentColor" stroke-width="2.4"><rect x="5" y="3" width="14" height="18"/><path d="M8 8h8M8 12h8"/></svg>Advanced Security</h4>
      <p>Employing advanced security measures for protection against potential threats and unauthorized access.</p>
    </article>
    <article class="feature wide" style="left:359px;top:599px;width:157px">
      <h4><svg viewBox="0 0 24 24" fill="none" stroke="currentColor" stroke-width="2.4"><rect x="3" y="14" width="18" height="6"/><rect x="6" y="8" width="5" height="6"/><rect x="13" y="3" width="5" height="6"/></svg>Large Facility Capacity</h4>
      <p>Our 4MW facility capacity underscores the infrastructure's ability to accommodate high-energy demands.</p>
    </article>
    <article class="feature" style="left:28px;top:657px;width:149px">
      <h4><svg viewBox="0 0 24 24" fill="none" stroke="currentColor" stroke-width="2.4"><path d="M4 14v-2a8 8 0 0116 0v2"/><rect x="3" y="13" width="4" height="6"/><rect x="17" y="13" width="4" height="6"/></svg>Expert Support</h4>
      <p>Benefit from expert support, ensuring assistance and guidance to optimize equipment and resolve issues effectively.</p>
    </article>
    <article class="feature" style="left:193px;top:657px;width:149px">
      <h4><svg viewBox="0 0 24 24" fill="none" stroke="currentColor" stroke-width="2.4"><circle cx="12" cy="12" r="9"/><path d="M12 7v5l3 2"/></svg>Metered Usage</h4>
      <p>We exclusively bill you based on your usage, without exceptions! Leveraging state-of-the-art metering.</p>
    </article>
    <article class="feature wide" style="left:359px;top:657px;width:157px">
      <h4><svg viewBox="0 0 24 24" fill="none" stroke="currentColor" stroke-width="2.4"><circle cx="9" cy="8" r="4"/><path d="M2 21c0-4 3-6 7-6M15 14l3 3 4-5"/></svg>Direct Equipment Access</h4>
      <p>Effectively command your operations with a comprehensive, full-spectrum control system - you got the keys.</p>
    </article>
  </section>

  <footer class="footer">www.quillfernvaults.example</footer>
</main>
</body>
</html>
```